Dew and Willow med spa needs an awesome eye catching billboard ad

We need a billboard ad design for a Med Spa with location sin Davenport and Windermere FL A medical spa where the beauty of nature meets the power of science to treat the whole person, mind, body and soul.

Marigold Radiance Med Spa is a medical spa where the beauty of nature meets the power of science to create gorgeous, youthful looking skin. Located in Davenport, Florida, but also serving Four Corners, Celebration, and Windermere, Florida, the talented professional team brings decades of experience in world-class skin care to provide holistic, science-backed aesthetic services and health coaching.

Industry/Entity Type

Spa

Colors
fbee3e
fece3e
eea4c8
e667a6
fbee3d

Requirements
Must have
• Locations in Davenport and Dr Phillips
Phone 407-555-0148
website www.dewandwillow-example.com

Boards for each:
Aesthetic Treatments
Cosmetic Injectables
Quoria facial
add color vs too many earthtones, to catch the eye perhaps using yellow, something that catches the eye and stands out from the normal everyday
Thank you!!!!
Nice to have
• Boards for each:
Aesthetic Treatments
Cosmetic Injectables
Quoria facial
add color vs too many earthtones, to catch the eye
photos that match services,
Thank you!!!!

```html
<!DOCTYPE html>
<html lang="en">
<head>
<meta charset="utf-8">
<title>Marigold Radiance Med Spa – Billboard</title>
<link rel="stylesheet" href="https://fonts.googleapis.com/css2?family=Cinzel:wght@400;700&family=Marcellus&display=swap">
<style>
  :root {
    --stage: #e8e8e6;
    --board: #fdfcf8;
    --gold: #c9a13a;
    --sun: #fbee3e;
    --marigold: #fece3e;
    --rose: #e667a6;
    --rose-soft: #eea4c8;
    --ink: #4c4c4e;
  }
  * { margin: 0; padding: 0; box-sizing: border-box; }
  html, body {
    width: 1029px; height: 1200px; overflow: hidden;
    background: var(--stage);
  }
  .canvas {
    position: relative; width: 1029px; height: 1200px;
    display: flex; align-items: center; justify-content: center;
  }
  .billboard {
    position: relative; width: 1029px; height: 504px;
    background: linear-gradient(180deg, #ffffff 0%, var(--board) 100%);
    overflow: hidden;
  }
  .petals { position: absolute; }
  .petals--top-left { left: 0; top: 0; width: 170px; height: 150px; }
  .petals--bottom-left { left: 0; bottom: 0; width: 120px; height: 80px; }
  .petals--right { right: 0; top: 0; width: 150px; height: 260px; }

  .model-photo {
    position: absolute; left: 614px; top: 0; width: 415px; height: 504px;
  }

  .brand {
    position: absolute; left: 0; top: 0; width: 620px; height: 330px;
    text-align: center;
  }
  .brand__dot {
    position: absolute; left: 297px; top: 62px;
    width: 26px; height: 26px; border-radius: 50%; background: var(--marigold);
  }
  .brand__name {
    position: absolute; left: 0; width: 620px; top: 120px;
    font-family: "Cinzel", serif; font-weight: 400; color: var(--gold);
    font-size: 50px; letter-spacing: 18px; text-indent: 18px; line-height: 1;
  }
  .brand__tagline {
    position: absolute; left: 0; width: 620px; top: 196px;
    font-family: "Cinzel", serif; font-weight: 400; color: var(--gold);
    font-size: 21px; letter-spacing: 8px; text-indent: 8px; line-height: 1;
  }
  .brand__web {
    position: absolute; left: 0; width: 620px; top: 240px;
    font-family: "Marcellus", serif; color: var(--ink);
    font-size: 19px; letter-spacing: 0.5px; line-height: 1;
  }
  .brand__locations {
    position: absolute; left: 0; width: 620px; top: 278px;
    font-family: "Marcellus", serif; color: var(--rose);
    font-size: 18px; letter-spacing: 3px; text-indent: 3px; line-height: 1;
  }
  .brand__locations-dot {
    display: inline-block; width: 7px; height: 7px; border-radius: 50%;
    background: var(--marigold); margin: 0 12px; vertical-align: middle;
  }
  .service-band {
    position: absolute; left: 0; top: 330px; width: 620px; height: 48px;
    background: linear-gradient(90deg, var(--marigold) 0%, var(--sun) 40%, rgba(251,238,62,0) 100%);
  }
  .service-band__label {
    position: absolute; left: 58px; top: 6px;
    font-family: "Cinzel", serif; font-weight: 700; color: var(--ink);
    font-size: 35px; line-height: 1; white-space: nowrap;
  }
  .phone {
    position: absolute; left: 0; width: 620px; top: 408px; text-align: center;
    font-family: "Marcellus", serif; color: var(--ink);
    font-size: 58px; line-height: 1;
  }
</style>
</head>
<body>
<main class="canvas">
  <section class="billboard">
    <svg class="petals petals--top-left" role="img" aria-label="Soft yellow flower petals decoration" viewBox="0 0 170 150">
      <defs>
        <radialGradient id="petalGlowA" cx="0" cy="0" r="1">
          <stop offset="0" stop-color="#fece3e" stop-opacity="0.75"/>
          <stop offset="1" stop-color="#ffffff" stop-opacity="0"/>
        </radialGradient>
      </defs>
      <rect width="170" height="150" fill="url(#petalGlowA)"/>
    </svg>
    <svg class="petals petals--bottom-left" role="img" aria-label="Soft pink flower petals decoration" viewBox="0 0 120 80">
      <defs>
        <radialGradient id="petalGlowB" cx="0.3" cy="1" r="0.9">
          <stop offset="0" stop-color="#eea4c8" stop-opacity="0.8"/>
          <stop offset="1" stop-color="#ffffff" stop-opacity="0"/>
        </radialGradient>
      </defs>
      <rect width="120" height="80" fill="url(#petalGlowB)"/>
    </svg>

    <svg class="model-photo" role="img" aria-label="Photo of a smiling woman in white with long flowing hair" viewBox="0 0 415 504" preserveAspectRatio="none">
      <defs>
        <linearGradient id="photoTone" x1="0" y1="0" x2="1" y2="1">
          <stop offset="0" stop-color="#f7f5f1"/>
          <stop offset="0.45" stop-color="#e6d3b6"/>
          <stop offset="0.7" stop-color="#f1ebe3"/>
          <stop offset="1" stop-color="#f6f4f1"/>
        </linearGradient>
      </defs>
      <rect width="415" height="504" fill="url(#photoTone)"/>
    </svg>

    <svg class="petals petals--right" role="img" aria-label="Soft yellow flower petals decoration" viewBox="0 0 150 260">
      <defs>
        <radialGradient id="petalGlowC" cx="1" cy="0.35" r="0.9">
          <stop offset="0" stop-color="#fbee3e" stop-opacity="0.7"/>
          <stop offset="1" stop-color="#ffffff" stop-opacity="0"/>
        </radialGradient>
      </defs>
      <rect width="150" height="260" fill="url(#petalGlowC)"/>
    </svg>

    <div class="brand">
      <span class="brand__dot"></span>
      <h1 class="brand__name">MARIGOLD</h1>
      <p class="brand__tagline">RADIANCE MED SPA</p>
      <p class="brand__web">WWW.DEWANDWILLOW-EXAMPLE.COM</p>
      <p class="brand__locations">DAVENPORT<span class="brand__locations-dot"></span>DR PHILLIPS</p>
    </div>

    <div class="service-band">
      <h2 class="service-band__label">COSMETIC INJECTABLES</h2>
    </div>

    <p class="phone">407-555-0148</p>
  </section>
</main>
</body>
</html>
```